Business Card for Industrial Distributor

We need a business card design for an industrial distributor. We sell machine parts for the manufacturing and oil industry. We would like the cards to look clean and modern but with a touch of industry.

Our colors are blue/white.

Please feel free to visit our website www.korvelpartsco.com

Target Market(s)

mexican manufacturers in the automobile/aerospace industry

Industry/Entity Type

Industrial

Colors
ffffff
0555a3

```html
<!DOCTYPE html>
<html lang="en">
<head>
<meta charset="utf-8">
<title>Korvel Business Card</title>
<link href="https://fonts.googleapis.com/css2?family=Montserrat:wght@400;500;600;800&display=swap" rel="stylesheet">
<style>
  :root {
    --bg: #3a3a3c;
    --card: #020203;
    --indigo: #2e3aa6;
    --sky: #1a78d0;
    --brand-blue: #2f3fb0;
    --name-blue: #1c86d8;
    --white: #ffffff;
    --text-light: #e8e8ee;
  }
  * { margin: 0; padding: 0; box-sizing: border-box; }
  html, body { width: 1200px; height: 900px; overflow: hidden; }
  body {
    background: var(--bg);
    font-family: "Montserrat", Arial, sans-serif;
    position: relative;
  }
  .card {
    position: absolute;
    width: 600px;
    height: 343px;
    background: var(--card);
    border-radius: 22px;
    overflow: hidden;
    box-shadow: 0 12px 30px rgba(0,0,0,0.45);
  }
  .card-front { left: 70px; top: 60px; }
  .card-back { left: 530px; top: 490px; }
  .card-shapes { position: absolute; inset: 0; }

  .front-mark {
    position: absolute;
    left: 0; right: 0; top: 95px;
    display: flex; align-items: center; justify-content: center; gap: 18px;
  }
  .mark-dot {
    width: 64px; height: 64px; border-radius: 50%;
    background: var(--brand-blue);
  }
  .front-name {
    font-weight: 800; font-size: 58px; color: var(--brand-blue);
  }
  .front-url {
    position: absolute; left: 36px; bottom: 12px;
    font-size: 15px; font-weight: 500; color: var(--white);
    letter-spacing: 0.3px;
  }
  .front-url b { font-weight: 800; }

  .back-brand {
    position: absolute; left: 36px; top: 58px;
    display: flex; align-items: center; gap: 14px;
  }
  .back-brand .mark-dot { width: 52px; height: 52px; }
  .back-name {
    font-weight: 800; font-size: 56px; color: var(--brand-blue); line-height: 1;
  }
  .person {
    position: absolute; right: 30px; top: 128px; text-align: right;
  }
  .person-name {
    font-size: 22px; font-weight: 600; color: var(--name-blue); letter-spacing: 1px;
  }
  .person-role { font-size: 13px; color: var(--white); margin-top: 2px; }
  .divider {
    position: absolute; left: 110px; right: 30px; top: 188px;
    height: 1.5px; background: var(--white);
  }
  .contact {
    position: absolute; left: 118px; top: 206px;
    list-style: none; color: var(--text-light); font-size: 15px; line-height: 20px;
  }
  .contact li { display: flex; align-items: center; gap: 10px; }
  .contact .icon { width: 12px; height: 12px; flex: none; }
  .contact .accent { color: var(--name-blue); }
</style>
</head>
<body>

  <section class="card card-front" aria-label="Card front">
    <svg class="card-shapes" viewBox="0 0 600 343" aria-hidden="true">
      <rect x="0" y="329" width="600" height="14" fill="var(--sky)"/>
      <polygon points="0,300 255,300 300,343 0,343" fill="var(--indigo)"/>
    </svg>
    <div class="front-mark">
      <span class="mark-dot"></span>
      <span class="front-name">Korvel</span>
    </div>
    <p class="front-url">www.<b>korvelpartsco</b>.com</p>
  </section>

  <section class="card card-back" aria-label="Card back">
    <svg class="card-shapes" viewBox="0 0 600 343" aria-hidden="true">
      <polygon points="440,225 600,225 600,292 420,292" fill="var(--indigo)"/>
      <polygon points="0,326 405,326 415,306 425,306 412,334 0,334" fill="var(--sky)"/>
    </svg>
    <div class="back-brand">
      <span class="mark-dot"></span>
      <span class="back-name">Korvel</span>
    </div>
    <div class="person">
      <p class="person-name">Marek Holloway</p>
      <p class="person-role">Director</p>
    </div>
    <div class="divider"></div>
    <ul class="contact">
      <li>P.O. Box 4418</li>
      <li>Lakeview Falls, MI 49930</li>
      <li>
        <svg class="icon" viewBox="0 0 12 12"><path d="M2 1 L4.5 1 L5.5 3.5 L4 4.8 Q5 7 7.2 8 L8.5 6.5 L11 7.5 L11 10 Q11 11 10 11 Q1 10 1 2 Q1 1 2 1Z" fill="var(--name-blue)"/></svg>
        +418 5931-2087
      </li>
      <li>
        <svg class="icon" viewBox="0 0 12 12"><rect x="1" y="2.5" width="10" height="7" rx="1" fill="none" stroke="var(--name-blue)" stroke-width="1.3"/><path d="M1.5 3 L6 6.5 L10.5 3" fill="none" stroke="var(--name-blue)" stroke-width="1.3"/></svg>
        info@korvelpartsco.com
      </li>
      <li>
        <svg class="icon" viewBox="0 0 12 12"><circle cx="6" cy="6" r="5" fill="none" stroke="var(--name-blue)" stroke-width="1.2"/><ellipse cx="6" cy="6" rx="2.2" ry="5" fill="none" stroke="var(--name-blue)" stroke-width="1"/><line x1="1" y1="6" x2="11" y2="6" stroke="var(--name-blue)" stroke-width="1"/></svg>
        <span>www.<span class="accent">korvelpartsco</span>.com</span>
      </li>
    </ul>
  </section>

</body>
</html>
```